Copper Lantern

Need a business card for our restaurant. Restaurant and Bar in the mountains of North Idaho. Rustic looking card

rustic design, wood and metal looking, primarily neutral colors

• Name, address, phone number, website, email address

```html
<!DOCTYPE html>
<html lang="en">
<head>
<meta charset="utf-8">
<title>Copper Lantern — Business Card</title>
<link href="https://fonts.googleapis.com/css2?family=Montserrat:wght@400;700&display=swap" rel="stylesheet">
<style>
  :root {
    --backdrop: #d5d9d9;
    --card-stock: #efefed;
    --ink: #111111;
    --ink-soft: #3a3a3a;
    --edge: #0c0c0c;
  }
  * { margin: 0; padding: 0; box-sizing: border-box; }
  html, body {
    width: 1200px; height: 881px; overflow: hidden;
    background: var(--backdrop);
    font-family: "Montserrat", sans-serif;
    color: var(--ink);
  }
  .sheet {
    position: relative; width: 1200px; height: 881px;
    display: flex; align-items: center; justify-content: center; gap: 60px;
  }
  .card {
    width: 500px; height: 286px;
    background: var(--card-stock);
    border-bottom: 6px solid var(--edge);
    position: relative;
    overflow: hidden;
    box-shadow: 0 10px 24px rgba(0,0,0,0.12);
  }
  /* Contact side */
  .card--contact .identity {
    position: absolute; right: 250px; top: 98px; text-align: right; white-space: nowrap;
  }
  .identity .person-name { font-weight: 700; font-size: 24px; letter-spacing: 0.2px; line-height: 1.2; }
  .identity .person-title { font-weight: 400; font-size: 14px; color: var(--ink-soft); margin-top: 4px; }
  .divider {
    position: absolute; left: 264px; top: 90px; width: 2px; height: 74px; background: var(--ink);
  }
  .contact-list {
    position: absolute; left: 280px; top: 96px; list-style: none;
    font-size: 14px; color: var(--ink-soft); white-space: nowrap;
  }
  .contact-list li { display: flex; align-items: center; gap: 7px; height: 22px; }
  .contact-list svg { width: 11px; height: 11px; fill: var(--ink); flex: none; }
  .address {
    position: absolute; left: 0; right: 0; top: 204px; text-align: center;
    font-size: 14px; color: var(--ink-soft);
  }
  /* Brand side */
  .card--brand { display: flex; align-items: center; justify-content: center; gap: 12px; }
  .brand-dot { width: 16px; height: 16px; border-radius: 50%; background: var(--ink); }
  .brand-name { font-weight: 700; font-size: 26px; letter-spacing: 2px; text-transform: uppercase; white-space: nowrap; }
</style>
</head>
<body>
<main class="sheet">
  <section class="card card--contact">
    <div class="identity">
      <p class="person-name">Owen Callister</p>
      <p class="person-title">Managing Director</p>
    </div>
    <div class="divider"></div>
    <ul class="contact-list">
      <li>
        <svg viewBox="0 0 12 12" aria-hidden="true"><path d="M1 4c0-2 2-3 5-3s5 1 5 3l-2 1-1-2H4L3 5 1 4zM2 6h8l1 5H1z"/></svg>
        123 456 789
      </li>
      <li>
        <svg viewBox="0 0 12 12" aria-hidden="true"><path d="M0 2h12v8H0z M1 3l5 4 5-4" stroke="#efefed" stroke-width="1"/></svg>
        info@yourgmail.com
      </li>
      <li>
        <svg viewBox="0 0 12 12" aria-hidden="true"><circle cx="6" cy="6" r="6"/></svg>
        www.yourwebsite.com
      </li>
    </ul>
    <p class="address">Your address, City State, Zip 1234</p>
  </section>

  <section class="card card--brand">
    <span class="brand-dot"></span>
    <span class="brand-name">Copper Lantern</span>
  </section>
</main>
</body>
</html>
```